VOR Exterior Coatings

double sided. the front i want the name of the business each word on a new line with the VOR being bigger. id like teal, black and white colors. the back i want my contact info. Flat, no gloss. Something professional and I want to feel the letters bump put of the card. if possible maybe a paint sprayer in corner. not a car paint spray. (no tank on top of gun)
no vehicle paint sprayers. that means no tank on top of the gun. doesn't have to have a sprayer. black/dark background on the front. white back ground on back with info

```html
<!DOCTYPE html>
<html lang="en">
<head>
<meta charset="utf-8">
<title>VOR Exterior Coatings – Business Card</title>
<link rel="stylesheet" href="https://fonts.googleapis.com/css2?family=Oswald:wght@600&family=Montserrat:wght@700&family=Open+Sans:wght@400&display=swap">
<style>
  :root {
    --teal: #17a2a6;
    --ink: #0b0b0b;
    --paper: #ffffff;
    --canvas: #e9eaea;
    --spray-tone: #2e3a3b;
  }
  * { box-sizing: border-box; margin: 0; padding: 0; }
  html, body { width: 1200px; height: 900px; overflow: hidden; }
  body {
    background: var(--canvas);
    font-family: "Open Sans", sans-serif;
    position: relative;
  }
  .card {
    position: absolute;
    left: 270px;
    width: 660px;
    height: 377px;
    border-radius: 24px;
    overflow: hidden;
    box-shadow: 0 4px 14px rgba(0,0,0,0.12);
  }
  .card--front { top: 52px; background: var(--ink); }
  .card--back  { top: 471px; background: var(--paper); color: var(--ink); }

  .wordmark {
    position: absolute;
    font-family: "Oswald", sans-serif;
    font-weight: 600;
    text-transform: uppercase;
    line-height: 1;
    white-space: nowrap;
  }
  .wordmark__big, .wordmark__small { display: block; letter-spacing: 2px; }

  .card--front .wordmark {
    color: var(--teal);
    left: 50%;
    top: 112px;
    transform: translateX(-50%);
    text-align: center;
  }
  .card--front .wordmark__big { font-size: 120px; }
  .card--front .wordmark__small { font-size: 40px; margin-top: 6px; }

  .sprayer-art {
    position: absolute;
    left: 370px;
    top: 44px;
    width: 150px;
    height: 56px;
    border-radius: 8px;
    background: linear-gradient(90deg, transparent, var(--spray-tone));
  }

  .card--back .wordmark {
    color: var(--ink);
    left: 50%;
    top: 34px;
    transform: translateX(-50%);
    text-align: center;
  }
  .card--back .wordmark__big { font-size: 88px; }
  .card--back .wordmark__small { font-size: 30px; margin-top: 2px; }

  .person {
    position: absolute;
    right: 372px;
    top: 222px;
    text-align: right;
  }
  .person__name {
    font-family: "Montserrat", sans-serif;
    font-weight: 700;
    font-size: 27px;
    color: var(--teal);
    letter-spacing: 0.5px;
    white-space: nowrap;
  }
  .person__role { font-size: 20px; color: var(--ink); margin-top: -2px; }

  .divider {
    position: absolute;
    left: 310px;
    top: 186px;
    width: 2px;
    height: 76px;
    background: var(--ink);
  }

  .contacts {
    position: absolute;
    left: 330px;
    top: 180px;
    list-style: none;
  }
  .contacts li {
    display: flex;
    align-items: center;
    gap: 10px;
    font-size: 19px;
    line-height: 28px;
    color: var(--ink);
    white-space: nowrap;
  }
  .contacts svg { width: 16px; height: 16px; flex: none; fill: var(--teal); }

  .address {
    position: absolute;
    left: 0; right: 0;
    top: 300px;
    text-align: center;
    font-size: 20px;
    color: var(--ink);
  }
</style>
</head>
<body>

  <section class="card card--front" aria-label="Card front">
    <div class="sprayer-art" role="img" aria-label="Sketch of a handheld paint sprayer releasing a fine mist"></div>
    <h1 class="wordmark">
      <span class="wordmark__big">VOR</span>
      <span class="wordmark__small">Exterior Coatings</span>
    </h1>
  </section>

  <section class="card card--back" aria-label="Card back">
    <div class="wordmark" aria-label="VOR Exterior Coatings">
      <span class="wordmark__big">VOR</span>
      <span class="wordmark__small">Exterior Coatings</span>
    </div>

    <div class="person">
      <p class="person__name">DANIEL HARPER</p>
      <p class="person__role">Manager</p>
    </div>

    <div class="divider"></div>

    <ul class="contacts">
      <li>
        <svg viewBox="0 0 16 16" aria-hidden="true"><path d="M3.6 1.2l2.3 2.6-1.2 1.9a9 9 0 0 0 5.6 5.6l1.9-1.2 2.6 2.3-1.5 2.3C7.6 14.6 1.4 8.4 1.3 2.7z"/></svg>
        555-014-2290
      </li>
      <li>
        <svg viewBox="0 0 16 16" aria-hidden="true"><path d="M1 3h14v10H1zM2.2 4.2v.4L8 8.8l5.8-4.2v-.4z"/></svg>
        hello@vormail.net
      </li>
      <li>
        <svg viewBox="0 0 16 16" aria-hidden="true"><path d="M8 1a7 7 0 1 0 0 14A7 7 0 0 0 8 1zm0 4.2a2.8 2.8 0 1 1 0 5.6 2.8 2.8 0 0 1 0-5.6z"/></svg>
        www.vorcoatings.net
      </li>
    </ul>

    <p class="address">Your address, city, state, ZIP 0000</p>
  </section>

</body>
</html>
```